Design the Business card for NetVaultic

Business card required for a professional Cyber Security business.
Company Logo and Icon has already been provided however I would like other options for the logo and icon to compare to. Alternatively, please refine/enhance the image of the logo.icon I have already provided.

If you are going to use the provided logo and icon, I was thinking that the company raised Logo on White background would serve well on the front of the card. See attached. AND, a large company raised stand-alone icon to appear on black background on the back of the card with tagline 'Cyber Risk Management, Governance and Consulting' or 'Cyber Security for your Business' See attached.
Alternatively, provide your own design for the logo and icon.

Target Market(s)

Enterprise, Government, Financial.

Contact Information for Business Card

Tavin Orloweth
Founder and CEO

Email Address
Mobile Number
Website URL
LinkedIn URL

Logo Text

NetVaultic - see attached example of logo

Font styles to use
Other font styles liked:
• Berlin Sans FB

Requirements
Must have
• Clean large and bold icon on the back with tagline.
• Horizontal alignment,
Nice to have
• Round edges.
• Raised Logo/Icon
Should not have
• An unprofessional look and feel.

```html
<!DOCTYPE html>
<html lang="en">
<head>
<meta charset="utf-8">
<title>NetVaultic Business Card</title>
<link rel="stylesheet" href="https://fonts.googleapis.com/css2?family=Roboto:wght@400;700&family=Roboto+Condensed:wght@500;700&family=Ubuntu:wght@400;500&display=swap">
<style>
  :root {
    --page: #e9e6e1;
    --card-white: #f7f7f6;
    --card-black: #17191c;
    --brand-blue: #1b6fc2;
    --tag-blue: #4f6fd0;
    --accent-yellow: #f2b01e;
    --text-grey: #4a4a4a;
    --faint-blue: #dfe6f3;
  }
  html, body {
    margin: 0;
    padding: 0;
    width: 1200px;
    height: 960px;
    overflow: hidden;
    background: var(--page);
  }
  .canvas {
    position: relative;
    width: 1200px;
    height: 960px;
  }
  .card {
    position: absolute;
    width: 600px;
    height: 343px;
    box-shadow: 0 3px 8px rgba(0,0,0,0.25);
    overflow: hidden;
  }
  .card-front {
    left: 314px;
    top: 113px;
    background: var(--card-white);
  }
  .card-back {
    left: 311px;
    top: 472px;
    background: var(--card-black);
  }
  .brand {
    position: absolute;
    left: 42px;
    top: 42px;
    display: flex;
    align-items: center;
    gap: 14px;
  }
  .brand-dot {
    width: 62px;
    height: 62px;
    border-radius: 50%;
    background: var(--brand-blue);
  }
  .brand-name {
    font-family: "Ubuntu", sans-serif;
    font-weight: 500;
    font-size: 40px;
    color: var(--brand-blue);
    line-height: 1;
  }
  .front-accent {
    position: absolute;
    right: -60px;
    bottom: -70px;
    width: 260px;
    height: 260px;
    border-radius: 50%;
    background: var(--faint-blue);
    opacity: 0.6;
  }
  .contact-list {
    position: absolute;
    left: 42px;
    top: 226px;
    margin: 0;
    padding: 0;
    list-style: none;
    font-family: "Roboto", sans-serif;
    font-size: 14px;
    color: var(--text-grey);
  }
  .contact-list li {
    display: flex;
    align-items: center;
    gap: 8px;
    height: 19.5px;
  }
  .contact-icon {
    width: 14px;
    height: 14px;
    flex: none;
  }
  .holder {
    position: absolute;
    right: 60px;
    top: 243px;
    text-align: right;
    font-family: "Roboto Condensed", sans-serif;
  }
  .holder-name {
    margin: 0;
    font-size: 21px;
    font-weight: 700;
    color: var(--brand-blue);
    line-height: 1.1;
  }
  .holder-title {
    margin: 2px 0 0;
    font-size: 15px;
    font-weight: 500;
    color: var(--accent-yellow);
  }
  .back-accent {
    position: absolute;
    left: -70px;
    top: 40px;
    width: 320px;
    height: 320px;
    border-radius: 50%;
    background: #20242c;
  }
  .back-brand {
    position: absolute;
    right: 43px;
    top: 228px;
    text-align: right;
    font-family: "Ubuntu", sans-serif;
  }
  .back-brand .brand-name {
    font-size: 40px;
  }
  .tagline {
    margin: 8px 0 0;
    font-size: 17px;
    line-height: 1.1;
  }
  .tagline-primary { color: var(--tag-blue); }
  .tagline-secondary { color: var(--accent-yellow); margin-top: 0; }
</style>
</head>
<body>
<main class="canvas">
  <section class="card card-front" aria-label="Card front">
    <div class="front-accent"></div>
    <div class="brand">
      <span class="brand-dot"></span>
      <span class="brand-name">NetVaultic</span>
    </div>
    <ul class="contact-list">
      <li>
        <svg class="contact-icon" viewBox="0 0 14 14" aria-hidden="true"><rect x="3.5" y="0.5" width="7" height="13" rx="1.2" fill="var(--brand-blue)"/><rect x="4.7" y="2" width="4.6" height="8.5" fill="#fff"/></svg>
        555 014 2738
      </li>
      <li>
        <svg class="contact-icon" viewBox="0 0 14 14" aria-hidden="true"><rect x="0.5" y="3" width="13" height="9" fill="var(--brand-blue)"/><path d="M1 3.5 L7 8 L13 3.5" stroke="#fff" stroke-width="1.2" fill="none"/></svg>
        tavin@netvaultic.com
      </li>
      <li>
        <svg class="contact-icon" viewBox="0 0 14 14" aria-hidden="true"><circle cx="7" cy="7" r="6" fill="var(--brand-blue)"/><path d="M1 7 H13 M7 1 C4 4 4 10 7 13 M7 1 C10 4 10 10 7 13" stroke="#fff" stroke-width="0.9" fill="none"/></svg>
        www.netvaultic.com
      </li>
      <li>
        <svg class="contact-icon" viewBox="0 0 14 14" aria-hidden="true"><circle cx="7" cy="7" r="6" fill="var(--brand-blue)"/></svg>
        netvaultic
      </li>
    </ul>
    <div class="holder">
      <p class="holder-name">TAVIN ORLOWETH</p>
      <p class="holder-title">FOUNDER &amp; CEO</p>
    </div>
  </section>

  <section class="card card-back" aria-label="Card back">
    <div class="back-accent"></div>
    <div class="back-brand">
      <span class="brand-name">NetVaultic</span>
      <p class="tagline tagline-primary">Cyber Risk Management</p>
      <p class="tagline tagline-secondary">Governance &amp; Consulting</p>
    </div>
  </section>
</main>
</body>
</html>
```